Venture 482 - Lumora Book Cover

I am looking for a Lumora book cover for my book about "Venture 482".
The Book is Titled:
Venture 482 Ascended
Shaping Outcomes: Paths To Unlocking Cosmic Truths
Author is Dorian Pell
Here is a book description that may help you understand more about it:
Inspired by the genius of Edwin Marlowe, this comprehensive guide delves into the ancient wisdom and cutting-edge science behind the 482 method, a powerful tool for manifesting your desires. Whether you're seeking personal growth, financial success, or spiritual enlightenment, this book provides advanced techniques and methods to transform your dreams into reality.
Any questions please ask.
Thanks
Owen

```html
<!DOCTYPE html>
<html lang="en">
<head>
<meta charset="utf-8">
<title>Venture 482 Ascended — Dorian Pell</title>
<link href="https://fonts.googleapis.com/css2?family=Anton&family=Montserrat:wght@400;700;900&display=swap" rel="stylesheet">
<style>
  :root {
    --page-bg: #e4e4e4;
    --red-core: #ff1424;
    --red-mid: #d50f1d;
    --red-deep: #8e0a16;
    --red-edge: #6e0812;
    --white: #ffffff;
    --gold: #f7a800;
    --mandala: rgba(235, 225, 225, 0.22);
  }
  * { margin: 0; padding: 0; box-sizing: border-box; }
  html, body {
    width: 1200px; height: 1131px; overflow: hidden;
    background: var(--page-bg);
  }
  .cover {
    position: absolute; left: 239px; top: 20px;
    width: 722px; height: 1090px; overflow: hidden;
    background:
      repeating-radial-gradient(circle at 50% 54%, rgba(0,0,0,0) 0 60px, rgba(0,0,0,0.05) 60px 62px, rgba(0,0,0,0) 62px 120px),
      radial-gradient(circle at 50% 54%, var(--red-core) 0%, var(--red-mid) 30%, var(--red-deep) 62%, var(--red-edge) 100%);
  }
  .mandala {
    position: absolute; left: 388px; top: 228px;
    width: 284px; height: 284px; border-radius: 50%;
    background: radial-gradient(circle, rgba(255,255,255,0.18) 0%, var(--mandala) 45%, rgba(255,255,255,0) 72%);
  }
  .series {
    position: absolute; left: 100px; top: 226px;
    font: 700 74px/1 "Montserrat", sans-serif; letter-spacing: -2px;
    color: var(--white);
  }
  .number {
    position: absolute; left: 16px; width: 722px; top: 287px; text-align: center;
    font: 400 261px/1 "Anton", sans-serif; letter-spacing: 2px;
    color: var(--white);
    text-shadow: 4px 8px 14px rgba(90, 0, 8, 0.55);
  }
  .edition {
    position: absolute; left: 0; width: 722px; top: 572px; text-align: center;
    font: 700 46px/1 "Montserrat", sans-serif; letter-spacing: 26px; text-indent: 26px;
    color: var(--white);
  }
  .subtitle-lead {
    position: absolute; left: 0; width: 722px; top: 716px; text-align: center;
    font: 400 40px/1 "Montserrat", sans-serif;
    color: var(--white);
  }
  .subtitle {
    position: absolute; left: 0; width: 722px; top: 776px; text-align: center;
    font: 900 38px/42px "Montserrat", sans-serif;
    color: var(--gold);
  }
  .author {
    position: absolute; left: 0; width: 722px; top: 958px; text-align: center;
    font: 400 80px/1 "Anton", sans-serif; letter-spacing: 16px; text-indent: 16px;
    color: var(--white);
  }
</style>
</head>
<body>
  <main class="cover">
    <div class="mandala" role="img" aria-label="Fine-line sacred geometry mandala in pale silver"></div>
    <div class="series">VENTURE</div>
    <div class="number">482</div>
    <div class="edition">ASCENDED</div>
    <div class="subtitle-lead">SHAPING OUTCOMES:</div>
    <div class="subtitle">Paths to unlocking<br>cosmic truths</div>
    <div class="author">DORIAN PELL</div>
  </main>
</body>
</html>
```